Fitness Equipment & Service

I want to make the card eye catching and fun. We are called Corvane Motion Limited and we are based in Wales. We sell, install and service all types of fitness equipment from Skipping ropes, right through the Dumbbells, Kettle bells and Barbells through to state of the art Treadmills, Running Machines and Strength Equipment. We also design and install changing room furniture and lockers.

TYPOGRAPHY
We would like to use Futrura. Futura has an appearance of efficiency and forwardness. The typeface is derived
from simple geometric forms (near-perfect circles, triangles and squares) and is based on strokes of
near-even weight, which are low in contrast. This is most visible in the almost perfectly round stroke of
the o, which is nonetheless slightly ovoid.
The lowercase has tall ascenders, which rise above the cap line. The uppercase
characters present proportions similar to those of classical Roman capitals.

TYPOGRAPHIC CONSIDERATIONS
No Strike though
No Horizontal Scaling
No Drop Shadows
No Effects
Never use less than 120% Leading

OUR CORPORATE COLOURS
BRAND GUIDELINES
We were thinking that our primary colour palette consists of the Acid Green (Pantone 382) and Process Black.

We work closely with tquarly Ltd and would like to include their name on the card somewhere. I have attached images of the other brands that we work with as an idea or the small icons I have included that illustrate what we do?. I have very kindly been given permission to use any of the images off the files that I have included below, so I hope these help. I will include these below. I would be open to suggestions if it made the card more striking Can you do it?
Updates

Hi All, Just wanted to add a few thoughts but you are the guys with the creative visions (thats why are here) We are based in Wales, UK and we would be open to lots of different ideas on a theme but must be eye catching, Bold and FUN. If you can or think that the Welsh or any dragon could be put in there then go for it (its not a must have) We have also added some ideas for colour but again its over to you!! GO FOR IT ! Thanks and look forward to your visions! Owen

Hi All, Just thought I would sen through the contact details that need to be on the card. (if you want to play around with icons instead of the wording twitter, Facebook, go for it): Corvane Motion Limited Owen Pritchard Managing Director Mob: +44 (0)7582 913 406 e-mail: sales@corvanemotion.co.uk Web: Corvanemotion.co.uk twitter: @motionLetterbin Facebook: Corvane Motion Limited

```html
<!DOCTYPE html>
<html lang="en">
<head>
<meta charset="utf-8">
<title>Corvane Motion Limited – Business Card</title>
<link rel="stylesheet" href="https://fonts.googleapis.com/css2?family=Arimo:wght@400;700&display=swap">
<style>
  :root {
    --page-bg: #e9e7e2;
    --card-white: #ffffff;
    --navy-deep: #0e1f4d;
    --navy-mid: #173a86;
    --navy-light: #2556b0;
    --gold: #c9a24a;
    --gold-light: #e6c878;
    --ink-navy: #15204a;
    --text-light: #ffffff;
  }
  * { box-sizing: border-box; margin: 0; padding: 0; }
  html, body {
    width: 1200px; height: 950px; overflow: hidden;
    background: var(--page-bg);
    font-family: "Arimo", Arial, sans-serif;
  }
  .sheet {
    width: 1200px; height: 950px;
    display: flex; flex-direction: column;
    align-items: center; justify-content: center; gap: 40px;
  }
  .card {
    position: relative;
    width: 760px; height: 434px;
    border-radius: 4px;
    overflow: hidden;
    box-shadow: 0 6px 18px rgba(0,0,0,.18);
  }
  .card-front { background: var(--card-white); }
  .card-front .wave { position: absolute; inset: 0; width: 100%; height: 100%; }

  .brand {
    position: absolute; left: 70px; top: 36px;
    display: flex; flex-direction: column; align-items: flex-start; gap: 12px;
  }
  .brand-dot {
    width: 84px; height: 84px; border-radius: 50%;
    background: var(--navy-mid);
  }
  .brand-name {
    font-weight: 700; font-size: 22px; line-height: 1.2;
    color: var(--ink-navy);
    letter-spacing: .5px;
  }

  .contact {
    position: absolute; right: 52px; top: 186px;
    color: var(--text-light);
    text-align: right;
    font-size: 16px; line-height: 1.25;
  }
  .contact .person-name { font-weight: 700; font-size: 21px; }
  .contact-line {
    display: flex; justify-content: flex-end; align-items: center; gap: 10px;
  }
  .icon {
    width: 16px; height: 16px; flex: none;
    display: inline-flex; align-items: center; justify-content: center;
  }
  .icon-plain-square { width: 14px; height: 14px; background: var(--text-light); border-radius: 2px; }
  .icon-plain-circle { width: 15px; height: 15px; background: var(--text-light); border-radius: 50%; }

  .card-back {
    background: radial-gradient(ellipse at 45% 45%, var(--navy-light) 0%, var(--navy-mid) 45%, var(--navy-deep) 100%);
  }
  .back-brand {
    position: absolute; left: 0; right: 0; top: 90px;
    display: flex; flex-direction: column; align-items: center; gap: 16px;
  }
  .back-brand .brand-dot { background: var(--navy-deep); border: 4px solid #c8ccd6; width: 130px; height: 130px; }
  .back-brand .brand-name { color: var(--text-light); }
  .back-url {
    position: absolute; right: 120px; bottom: 70px;
    color: var(--text-light); font-size: 18px; line-height: 1.25; letter-spacing: 1px;
    display: flex; align-items: center; gap: 10px;
  }
  .back-url .rule { width: 60px; height: 1px; background: var(--text-light); }
</style>
</head>
<body>
<main class="sheet">

  <section class="card card-front" aria-label="Business card front">
    <svg class="wave" viewBox="0 0 760 434" preserveAspectRatio="none" aria-hidden="true">
      <defs>
        <linearGradient id="navyFill" x1="0" y1="0" x2="1" y2="1">
          <stop offset="0" stop-color="#2556b0"/>
          <stop offset="0.55" stop-color="#173a86"/>
          <stop offset="1" stop-color="#0e1f4d"/>
        </linearGradient>
        <linearGradient id="goldStroke" x1="0" y1="0" x2="1" y2="0">
          <stop offset="0" stop-color="#b88c32"/>
          <stop offset="0.5" stop-color="#e6c878"/>
          <stop offset="1" stop-color="#c9a24a"/>
        </linearGradient>
      </defs>
      <path d="M0,220 C120,300 300,300 420,240 S640,120 760,100 L760,434 L0,434 Z" fill="url(#navyFill)"/>
      <path d="M0,211 C120,290 300,290 420,230 S640,110 760,90" fill="none" stroke="url(#goldStroke)" stroke-width="7"/>
    </svg>

    <div class="brand">
      <span class="brand-dot"></span>
      <span class="brand-name">Corvane Motion Limited</span>
    </div>

    <div class="contact">
      <div class="person-name">Owen Pritchard</div>
      <div class="person-role">Managing Director</div>
      <div>2716 Harlow Crescent</div>
      <div>Cardigan Bay, NY 11208</div>
      <div class="contact-line">+44 (0)7582 913 406
        <svg class="icon" viewBox="0 0 16 16" aria-hidden="true"><rect x="4" y="1" width="8" height="14" rx="1.5" fill="none" stroke="#fff" stroke-width="1.6"/><circle cx="8" cy="12.5" r="0.9" fill="#fff"/></svg>
      </div>
      <div class="contact-line">sales@corvanemotion.co.uk
        <svg class="icon" viewBox="0 0 16 16" aria-hidden="true"><rect x="1" y="3" width="14" height="10" rx="1" fill="#fff"/><path d="M1.5,3.8 L8,9 L14.5,3.8" fill="none" stroke="#173a86" stroke-width="1.4"/></svg>
      </div>
      <div class="contact-line">Corvanemotion.co.uk <span class="icon"><span class="icon-plain-circle"></span></span></div>
      <div class="contact-line">@motionLetterbin <span class="icon"><span class="icon-plain-square"></span></span></div>
      <div class="contact-line">Corvane Motion Limited <span class="icon"><span class="icon-plain-square"></span></span></div>
    </div>
  </section>

  <section class="card card-back" aria-label="Business card back">
    <div class="back-brand">
      <span class="brand-dot"></span>
      <span class="brand-name">Corvane Motion Limited</span>
    </div>
    <div class="back-url"><span>www.corvanemotion.co.uk</span><span class="rule"></span></div>
  </section>

</main>
</body>
</html>
```